Industrial B2B Company Seeks Complete Redesign

We manufacture solid/liquid filtration equipment for manufacturers of chemicals, pharmaceuticals and mining products. We will be redesigning our website; our current design is outdated, and a more modern look is desired. Navigation can be improved. Call to action on the header, such as "Start Here". Video on home page. Designer should incorporate colors from our logo, at least the blues, the brown/gold is optional. Existing website can be found at www.BrindleSeparators.com. Also, we do not make water filters and references to water or water-like images should be avoided.
Number of Pages Required
1 page
Look and feel
Each slider illustrates characteristics of the customer's brand and the style your logo design should communicate.

```html
<!DOCTYPE html>
<html lang="en">
<head>
<meta charset="utf-8">
<title>Comprehensive Support</title>
<link rel="stylesheet" href="https://fonts.googleapis.com/css2?family=Inter:ital,wght@0,400;0,600;1,400&display=swap">
<style>
  :root {
    --navy: #17365c;
    --wave-top: #cdd7e3;
    --wave-mid: #e3e9f1;
    --page: #ffffff;
  }
  * { box-sizing: border-box; margin: 0; padding: 0; }
  html, body {
    width: 1200px;
    height: 550px;
    overflow: hidden;
    background: var(--page);
  }
  .support {
    position: relative;
    width: 1200px;
    height: 550px;
    overflow: hidden;
    font-family: "Inter", Arial, sans-serif;
    color: var(--navy);
  }
  .support__wave {
    position: absolute;
    left: 0;
    top: 0;
    width: 1200px;
    height: 320px;
  }
  .support__title {
    position: absolute;
    left: 0;
    width: 1186px;
    top: 220px;
    text-align: center;
    font-weight: 600;
    font-size: 61px;
    letter-spacing: 1.2px;
    line-height: 1;
  }
  .support__text {
    position: absolute;
    left: 190px;
    width: 886px;
    top: 332px;
    text-align: center;
    font-size: 17.2px;
    line-height: 25px;
  }
  .support__text a {
    color: inherit;
    text-decoration: underline;
    text-underline-offset: 3px;
    text-decoration-thickness: 1px;
  }
  .support__text em { font-style: italic; }
</style>
</head>
<body>
  <section class="support">
    <svg class="support__wave" viewBox="0 0 1200 320" aria-hidden="true">
      <defs>
        <linearGradient id="waveFade" x1="0" y1="0" x2="0" y2="1">
          <stop offset="0.15" stop-color="var(--wave-top)"/>
          <stop offset="0.5" stop-color="var(--wave-mid)"/>
          <stop offset="1" stop-color="var(--page)"/>
        </linearGradient>
      </defs>
      <path d="M0 92 C 110 62, 200 55, 304 55 C 470 55, 580 85, 700 112 C 800 134, 860 144, 930 144 C 1030 144, 1110 120, 1196 92 L 1196 320 L 0 320 Z" fill="url(#waveFade)"/>
    </svg>

    <h2 class="support__title">COMPREHENSIVE SUPPORT</h2>

    <p class="support__text">
      In addition to our <a href="#">extensive range of filtration equipment,</a><br>
      we offer comprehensive support in the form of <a href="#">filter media</a>, <a href="#">filtration process<br>consulting</a>, <a href="#">parts,</a> and <a href="#">rentals</a>.&nbsp; <em>Our team of application engineers is ready to assist you in achieving your process goals and objectives.</em>
    </p>
  </section>
</body>
</html>
```